Oil Field Service company needs professional business cards

Looking to clean up our current company business cards and look a little more professional. Brenwick Casing Services is a US based company that services the oil field. We deal with engineers, managers and oil rigs....................................................................................................................................................................................................................................................................................................................................................................................................

Target Market(s)

Oil and Gas professionals

Industry/Entity Type

Oil And Gas

Contact Information for Business Card

See attached photo as example

Font styles to use
Sans Serif

Colors
ec1f27

Requirements
Must have
• Company Logo, Name, Title, Cell, Office, Fax, Email.
• See attached photo
Nice to have
• External CRT, Internal CRT, Casing Crews, Torque Turn, Laydown Machine
Should not have
• Do not introduce any new pictures and keep it professional looking

```html
<!DOCTYPE html>
<html lang="en">
<head>
<meta charset="UTF-8">
<title>Brenwick Casing Services – Business Card</title>
<link href="https://fonts.googleapis.com/css2?family=Source+Sans+3:wght@400;600;700&display=swap" rel="stylesheet">
<style>
  :root {
    --stage: #000000;
    --brand-red: #e11b25;
    --slate: #465761;
    --logo-grey: #454d55;
    --white: #ffffff;
  }
  * { margin: 0; padding: 0; box-sizing: border-box; }
  html, body {
    width: 1200px; height: 900px; overflow: hidden;
    background: var(--stage);
    font-family: "Source Sans 3", Arial, sans-serif;
  }
  .canvas { position: relative; width: 1200px; height: 900px; }

  .card { position: absolute; top: 275px; width: 477px; height: 294px; overflow: hidden; }
  .card-front { left: 116px; background: var(--brand-red); border-radius: 0 50px 0 50px; }
  .card-back { left: 622px; top: 276px; height: 293px; background: var(--slate); border-radius: 50px 0 50px 0; }

  .wordmark { position: absolute; font-weight: 700; text-transform: uppercase; line-height: 1; }
  .wordmark .name { display: block; }
  .wordmark .tagline { display: block; letter-spacing: 3px; }
  .card-front .wordmark { left: 30px; top: 62px; width: 232px; text-align: center; color: var(--logo-grey); }
  .card-front .wordmark .name { font-size: 40px; letter-spacing: 1px; }
  .card-front .wordmark .tagline { font-size: 13px; margin-top: 8px; }

  .card-back .wordmark { left: 0; right: 0; top: 116px; text-align: center; color: var(--white); }
  .card-back .wordmark .name { font-size: 44px; letter-spacing: 1px; }
  .card-back .wordmark .tagline { font-size: 15px; margin-top: 14px; }

  .holder { position: absolute; right: 19px; top: 102px; text-align: right; color: var(--white); }
  .holder-name { font-size: 16px; font-weight: 600; line-height: 20px; }
  .holder-title { font-size: 13px; line-height: 20px; }

  .divider { position: absolute; left: 0; right: 0; top: 156px; height: 1.5px; background: var(--white); }

  .contacts { position: absolute; left: 63px; top: 167px; list-style: none; color: var(--white); }
  .contacts li { display: flex; align-items: center; height: 17px; font-size: 13px; }
  .contacts svg { width: 10px; height: 10px; margin-right: 8px; fill: var(--white); }

  .services { position: absolute; left: 63px; top: 245px; font-size: 13px; color: var(--white); }
</style>
</head>
<body>
<div class="canvas">

  <section class="card card-front" aria-label="Business card front">
    <div class="wordmark">
      <span class="name">Brenwick</span>
      <span class="tagline">Casing Services</span>
    </div>

    <div class="holder">
      <p class="holder-name">Cody Marlowe</p>
      <p class="holder-title">Area Manager</p>
    </div>

    <div class="divider"></div>

    <ul class="contacts">
      <li><svg viewBox="0 0 10 10" aria-hidden="true"><path d="M2 0.5 L3.6 2.6 L2.8 3.6 Q4 6 6.4 7.2 L7.4 6.4 L9.5 8 L8.4 9.5 Q1 8.5 0.5 1.6 Z"/></svg>(580) 555-0140</li>
      <li><svg viewBox="0 0 10 10" aria-hidden="true"><path d="M3 0.5 H7 V9.5 H3 Z M3.8 1.5 V7.5 H6.2 V1.5 Z M4.6 8 H5.4 V8.8 H4.6 Z"/></svg>(580) 555-0187</li>
      <li><svg viewBox="0 0 10 10" aria-hidden="true"><path d="M2.5 0.5 H7 V3.5 H9.5 V9.5 H0.5 V3.5 H2.5 Z M3.3 1.3 V3.5 H6.2 V1.3 Z M2 5 V6 H8 V5 Z"/></svg>(580) 555-0163</li>
      <li><svg viewBox="0 0 10 10" aria-hidden="true"><path d="M0.5 2 H9.5 V8.5 H0.5 Z M1.4 2.8 L5 5.4 L8.6 2.8 Z"/></svg>cody.marlowe@brenwick.com</li>
    </ul>

    <p class="services">Laydown Machine | Casing Crew | Mud Tool | Torque Turn</p>
  </section>

  <section class="card card-back" aria-label="Business card back">
    <div class="wordmark">
      <span class="name">Brenwick</span>
      <span class="tagline">Casing Services</span>
    </div>
  </section>

</div>
</body>
</html>
```